Modern Business Card

Modern professional business card with more than just logo and demographic info. Something memorable.

We are a trendy/modern chiropractic group with an emphasis on neurology, hence the minimalist-type brain logo. We want to convey that modern and technical aspect with professionalism and the elite nature of our practice environment.

```html
<!DOCTYPE html>
<html lang="en">
<head>
<meta charset="utf-8">
<title>Vantage Chiropractic – Business Card</title>
<link href="https://fonts.googleapis.com/css2?family=Open+Sans:wght@400;700&display=swap" rel="stylesheet">
<style>
  :root {
    --backdrop: #d9d9d7;
    --card: #2d2e31;
    --accent: #3f7fd0;
    --ink: #f2f2f2;
    --muted: #d8d8d8;
    --shade-dark: #232427;
    --shade-light: #4a4b4f;
  }
  * { box-sizing: border-box; margin: 0; padding: 0; }
  html, body {
    width: 1200px; height: 801px; overflow: hidden;
    background: var(--backdrop);
    font-family: "Open Sans", Arial, sans-serif;
  }
  .sheet {
    position: relative; width: 1200px; height: 801px;
    display: flex; align-items: center; justify-content: center; gap: 60px;
  }
  .card {
    position: relative; width: 525px; height: 300px;
    background: var(--card);
    border-bottom: 3px solid var(--accent);
    overflow: hidden;
  }
  /* Front */
  .front__brand {
    position: absolute; left: 38px; top: 122px;
    display: flex; align-items: center; gap: 12px;
  }
  .brand-square { width: 30px; height: 30px; background: var(--accent); }
  .brand-name {
    color: var(--ink); font-weight: 400; font-size: 21px;
    letter-spacing: 1.5px; text-transform: uppercase; line-height: 1.15;
  }
  .front__divider {
    position: absolute; left: 282px; top: 40px; width: 2px; height: 212px;
    background: var(--accent);
  }
  .front__details { position: absolute; left: 300px; top: 46px; width: 210px; }
  .person-name {
    color: var(--accent); font-weight: 700; font-size: 18px;
    text-transform: uppercase; letter-spacing: .3px;
  }
  .person-role, .address { color: var(--muted); font-size: 13px; line-height: 1.45; }
  .person-role { margin-bottom: 10px; }
  .rule { height: 2px; background: var(--accent); margin: 12px -18px 12px -18px; }
  .contact { list-style: none; }
  .contact li {
    display: flex; align-items: center; gap: 6px;
    color: var(--muted); font-size: 12.5px; line-height: 1.6;
  }
  .contact svg { width: 11px; height: 11px; flex: none; }
  /* Back */
  .back__texture {
    position: absolute; right: 0; top: 0; width: 300px; height: 200px;
    background: linear-gradient(120deg, var(--shade-dark) 0%, #2f3033 55%, var(--shade-light) 100%);
    border-bottom-left-radius: 40px;
  }
  .back__brand {
    position: absolute; left: 36px; bottom: 40px;
    display: flex; align-items: center; gap: 14px;
  }
  .back__brand .brand-name { font-size: 30px; letter-spacing: 2px; }
</style>
</head>
<body>
<main class="sheet">
  <section class="card card--front" aria-label="Card front">
    <div class="front__brand">
      <span class="brand-square"></span>
      <p class="brand-name">Vantage<br>Chiropractic</p>
    </div>
    <div class="front__divider"></div>
    <div class="front__details">
      <h1 class="person-name">Daniel Verhoef</h1>
      <p class="person-role">President</p>
      <p class="address">1820 Harbor View Lane<br>Seacliff CA 92600</p>
      <div class="rule"></div>
      <ul class="contact">
        <li><svg viewBox="0 0 12 12"><path fill="var(--accent)" d="M2.5 1l2 2.2-1 1.3a6 6 0 0 0 4 4l1.3-1 2.2 2-1.3 1.5C5 11 1 7 1 2.3z"/></svg>555-014-2287</li>
        <li><svg viewBox="0 0 12 12"><rect x="1" y="2.5" width="10" height="7" rx="1" fill="var(--accent)"/><path d="M1.5 3l4.5 3.5L10.5 3" stroke="var(--card)" fill="none"/></svg>dan@vantagechiropractic.com</li>
        <li><svg viewBox="0 0 12 12"><circle cx="6" cy="6" r="5" fill="var(--accent)"/><path d="M1 6h10M6 1c-2 3-2 7 0 10M6 1c2 3 2 7 0 10" stroke="var(--card)" fill="none" stroke-width=".8"/></svg>www.vantagechiropractic.com</li>
      </ul>
    </div>
  </section>

  <section class="card card--back" aria-label="Card back">
    <div class="back__texture" role="img" aria-label="Tonal embossed brand decoration area"></div>
    <div class="back__brand">
      <p class="brand-name">Vantage<br>Chiropractic</p>
    </div>
  </section>
</main>
</body>
</html>
```